ULMIRA card Technical Architecture

Hello everyone ULMIRA: It is a consulting firm in Architecture and Construction. I require a card duplexing, sober, elegant, classic but not boring. Update 1: Use the following data for the card. Name: Gonzalo Pereda Mauricio Villalta Position: COO Twitter: @ulmiraAT Homepage: ulmira-example.com home address not include the participation of all thank you.

Target Market(s)

Construction companies, Architects and Consulting Engineers

Industry/Entity Type

Consulting

Contact Information for Business Card

Los campos que debe tener:
Nombre, Cargo, email, homepage y twitter

Font styles to use
Serif
Sans Serif
Other font styles liked:
• Me gustan playfair display, open sans y roboto, pero estoy sujeto a sus propuestas

Requirements
Must have
• Colors: Present combined proposals in white, red, gray and black Update 1: The two names must be clearly differentiated from the two surnames
Nice to have
• They are free to present their best proposals. I will bring them immediate feedback to the extent you can go see their designs. Complete data for card and logo files will give the winner the

```html
<!DOCTYPE html>
<html lang="es">
<head>
<meta charset="utf-8">
<title>ULMIRA – Business Card</title>
<link href="https://fonts.googleapis.com/css2?family=Lato:wght@300;400;700&display=swap" rel="stylesheet">
<style>
  :root {
    --stage: #2b2b2b;
    --paper: #f7f7f7;
    --red: #a3121c;
    --red-deep: #6e0a10;
    --red-mid: #8c0f17;
    --ink: #3a3a3a;
    --grey: #6f6f6f;
    --white: #ffffff;
  }
  * { box-sizing: border-box; margin: 0; padding: 0; }
  html, body { width: 1200px; height: 873px; overflow: hidden; }
  body {
    background: var(--stage);
    font-family: "Lato", sans-serif;
    position: relative;
  }
  .card {
    position: absolute;
    width: 540px;
    height: 309px;
    border-radius: 14px;
    overflow: hidden;
    box-shadow: 0 10px 30px rgba(0,0,0,.5);
  }

  /* Front */
  .card-front { left: 70px; top: 90px; background: var(--paper); }
  .front-brand {
    position: absolute; left: 55px; top: 72px; width: 240px; text-align: center;
  }
  .brand-name {
    font-weight: 300; font-size: 40px; letter-spacing: 12px; color: var(--ink);
    padding-left: 12px; line-height: 1.1;
  }
  .brand-rule { height: 1px; background: var(--red); margin: 4px 0 5px; }
  .brand-tagline {
    font-weight: 400; font-size: 12px; letter-spacing: 4.2px; color: var(--red);
  }
  .front-divider {
    position: absolute; left: 318px; top: 62px; width: 2px; height: 72px;
    background: linear-gradient(var(--paper), var(--ink), var(--paper));
  }
  .person { position: absolute; left: 340px; top: 70px; width: 190px; }
  .person-name { font-size: 15px; line-height: 1.25; color: var(--grey); }
  .given-name { font-weight: 700; color: var(--red); }
  .family-name { font-weight: 400; color: var(--grey); }
  .person-role { font-size: 11px; color: var(--ink); margin-top: 4px; }
  .contacts { position: absolute; left: 40px; top: 176px; list-style: none; }
  .contacts li {
    display: flex; align-items: center; gap: 9px;
    font-size: 14px; color: var(--ink); margin-bottom: 6px;
  }
  .contacts svg { width: 13px; height: 13px; fill: var(--red); flex: none; }
  .front-band {
    position: absolute; left: 0; bottom: 0; width: 100%; height: 42px;
    background: linear-gradient(var(--red), var(--red-mid));
    color: var(--white); font-weight: 700; font-size: 13px; letter-spacing: .5px;
    display: flex; align-items: center; justify-content: center;
  }

  /* Back */
  .card-back { left: 590px; top: 470px; }
  .back-texture {
    position: absolute; inset: 0;
    background: linear-gradient(135deg, var(--red) 0%, var(--red-mid) 55%, var(--red-deep) 100%);
  }
  .back-brand { position: absolute; left: 40px; top: 120px; width: 330px; }
  .back-brand .brand-name { color: var(--white); font-size: 44px; letter-spacing: 14px; padding-left: 0; }
  .back-brand .brand-rule { background: rgba(255,255,255,.6); }
  .back-brand .brand-tagline { color: var(--white); font-size: 14px; letter-spacing: 4.6px; }
  .back-web {
    margin-top: 8px; font-weight: 700; font-size: 13px; letter-spacing: 3px; color: #1e0204;
  }
</style>
</head>
<body>

<section class="card card-front">
  <div class="front-brand">
    <div class="brand-name">ULMIRA</div>
    <div class="brand-rule"></div>
    <div class="brand-tagline">ARQUITECTURA TÉCNICA</div>
  </div>
  <div class="front-divider"></div>
  <div class="person">
    <div class="person-name">
      <span class="given-name">Gonzalo</span> <span class="family-name">Pereda</span><br>
      <span class="given-name">Mauricio</span> <span class="family-name">Villalta</span>
    </div>
    <div class="person-role">Chief Operating Officer</div>
  </div>
  <ul class="contacts">
    <li><svg viewBox="0 0 16 16" aria-hidden="true"><path d="M3 1l3 3-2 2c1 2 3 4 5 5l2-2 3 3-2 3C7 15 1 9 0 4z"/></svg>555-014-7120</li>
    <li><svg viewBox="0 0 16 16" aria-hidden="true"><path d="M0 3h16v10H0z M0 3l8 6 8-6"/></svg>gonzalo@ulmira-example.com</li>
    <li><svg viewBox="0 0 16 16" aria-hidden="true"><circle cx="8" cy="8" r="7"/></svg>@ulmiraAT</li>
  </ul>
  <div class="front-band">www.ulmira-example.com</div>
</section>

<section class="card card-back">
  <div class="back-texture" role="img" aria-label="Red faceted polygon texture background"></div>
  <div class="back-brand">
    <div class="brand-name">ULMIRA</div>
    <div class="brand-rule"></div>
    <div class="brand-tagline">ARQUITECTURA TÉCNICA</div>
    <div class="back-web">www.ulmira-example.com</div>
  </div>
</section>

</body>
</html>
```